Business Card - Tidal Lanes

Need Business Card design for company named Tidal Lanes. Software development focused mainly on Brindle Orvix & Zelt Apps. I've attached our logo with both a black and white background. Please add trademark symbol to logo when using.

```html
<!DOCTYPE html>
<html lang="en">
<head>
<meta charset="utf-8">
<title>Tidal Lanes – Business Card</title>
<link rel="stylesheet" href="https://fonts.googleapis.com/css2?family=Source+Sans+3:wght@400;600;700&display=swap">
<style>
  :root {
    --canvas-bg: #e6e2db;
    --card-black: #0c0c0c;
    --brand-yellow: #f7c31c;
    --brand-orange: #f39a1f;
    --brand-red: #d7262b;
    --name-orange: #f5a21f;
    --text-light: #f2f2f2;
    --text-muted: #cfcfcf;
    --address-ink: #4a3208;
  }
  * { box-sizing: border-box; margin: 0; padding: 0; }
  html, body {
    width: 1200px;
    height: 720px;
    overflow: hidden;
    background: var(--canvas-bg);
    font-family: "Source Sans 3", Arial, sans-serif;
  }
  .canvas {
    position: relative;
    width: 1200px;
    height: 720px;
  }
  .card {
    position: absolute;
    top: 205px;
    width: 540px;
    height: 309px;
    background: var(--card-black);
    border-radius: 4px;
    overflow: hidden;
    box-shadow: 0 6px 18px rgba(0,0,0,0.18);
  }
  .card--front { left: 40px; }
  .card--back { left: 620px; }

  .card__wave {
    position: absolute;
    inset: 0;
    width: 100%;
    height: 100%;
  }

  .brand {
    position: absolute;
    display: flex;
    flex-direction: column;
    align-items: center;
    gap: 12px;
  }
  .brand__dot {
    border-radius: 50%;
    background: var(--brand-orange);
  }
  .brand__name {
    color: var(--text-light);
    font-weight: 700;
    letter-spacing: -0.5px;
    white-space: nowrap;
  }
  .card--front .brand { left: 48px; top: 62px; width: 170px; }
  .card--front .brand__dot { width: 58px; height: 58px; }
  .card--front .brand__name { font-size: 28px; }

  .contact {
    position: absolute;
    left: 252px;
    top: 40px;
    padding-left: 20px;
    border-left: 1px solid #6a6a6a;
    height: 96px;
  }
  .contact__name {
    color: var(--name-orange);
    font-weight: 700;
    font-size: 19px;
    line-height: 1.1;
  }
  .contact__title {
    color: var(--text-light);
    font-size: 13px;
    margin: 2px 0 8px;
  }
  .contact__line {
    display: flex;
    align-items: center;
    gap: 8px;
    color: var(--text-light);
    font-size: 15px;
    line-height: 1.55;
  }
  .contact__icon { width: 12px; height: 12px; flex: none; }

  .address {
    position: absolute;
    left: 150px;
    bottom: 20px;
    color: var(--address-ink);
    font-size: 14px;
    letter-spacing: 0.4px;
  }

  .card--back .brand {
    left: 0; right: 0;
    top: 78px;
  }
  .card--back .brand__dot { width: 70px; height: 70px; }
  .card--back .brand__name { font-size: 36px; }
  .website {
    position: absolute;
    left: 0; right: 0;
    bottom: 44px;
    text-align: center;
    color: var(--text-muted);
    font-size: 15px;
    letter-spacing: 0.8px;
  }
</style>
</head>
<body>
<main class="canvas">

  <section class="card card--front" aria-label="Business card front">
    <svg class="card__wave" viewBox="0 0 540 309" preserveAspectRatio="none" aria-hidden="true">
      <defs>
        <linearGradient id="band-fill" x1="0" x2="1" y1="0" y2="0">
          <stop offset="0" stop-color="var(--brand-orange)"/>
          <stop offset="0.45" stop-color="var(--brand-yellow)"/>
          <stop offset="1" stop-color="var(--brand-yellow)"/>
        </linearGradient>
      </defs>
      <path d="M0,248 C150,262 330,205 540,128 L540,309 L0,309 Z" fill="url(#band-fill)"/>
      <path d="M0,238 C150,254 330,190 540,112 L540,118 C330,200 150,258 0,244 Z" fill="var(--brand-red)"/>
    </svg>

    <div class="brand">
      <span class="brand__dot"></span>
      <span class="brand__name">Tidal Lanes</span>
    </div>

    <div class="contact">
      <p class="contact__name">Your Name</p>
      <p class="contact__title">Title</p>
      <p class="contact__line">
        <svg class="contact__icon" viewBox="0 0 12 12" aria-hidden="true">
          <rect x="3" y="0.5" width="6" height="11" rx="1.2" fill="var(--name-orange)"/>
          <rect x="4" y="2" width="4" height="6" fill="var(--card-black)"/>
        </svg>
        555-214-0370
      </p>
      <p class="contact__line">
        <svg class="contact__icon" viewBox="0 0 12 12" aria-hidden="true">
          <path d="M1,5 Q6,1 11,5 L10,7 L8,6 L8,5 L4,5 L4,6 L2,7 Z" fill="var(--name-orange)"/>
          <rect x="2" y="7" width="8" height="4" rx="1" fill="var(--name-orange)"/>
        </svg>
        555-608-4419
      </p>
    </div>

    <p class="address">4120 Harbor Row, Cove, FL 30000</p>
  </section>

  <section class="card card--back" aria-label="Business card back">
    <div class="brand">
      <span class="brand__dot"></span>
      <span class="brand__name">Tidal Lanes</span>
    </div>
    <p class="website">www.tidallanes.com</p>
  </section>

</main>
</body>
</html>
```